Global Beard Oil Review Business needs a refresh

topwhiskertonic.net is a global business who's mission is to curate all available beard oils from around the world, review and grade them and present this curated collection to the user of the website.

The scope of this job includes the web site design and the design of a suitable logo to be used in the site header.

The existing site can be seen on http://topwhiskertonic.net, however this is a mock-up only the style and logo should NOT be used. This is to give you an idea of the concept of the site only.

This job is for PSD design only.

See attached design brief for detailed design requirements.
Updates

Project Deadline Extended
Reason: Extending deadline by 5 days to allow for final submissions

Target Market(s)

Men's grooming / retail

Industry/Entity Type

Retail

Number of Pages Required

2 page

Font styles to use
Sans Serif

Requirements
Must have
• 1) Comparison Table
• 2) Side Bar
• 3) Header area
• 4) Photo of Delvin Marsk (attached - can be circular or "cut-out")
• 5) Cool beard-oriented custom design background (e.g., stylistic black/brown on brown/orange beard background. I envision this beard background "drawing" rather than photo based)
• (see attached design requirements for details)
Nice to have
• Signature style writing at top with name "Delvin Marsk"
Should not have
• Do NOT use the look & feel or logo from the existing site.

```html
<!DOCTYPE html>
<html lang="en">
<head>
<meta charset="utf-8">
<title>Top Whisker Tonic</title>
<link href="https://fonts.googleapis.com/css2?family=Lato:wght@400;700&family=Lobster&display=swap" rel="stylesheet">
<style>
:root{
  --teal:#3fb7b4;
  --orange:#f7962f;
  --green:#3aa635;
  --ink:#3c3c3c;
  --muted:#777;
  --hero-title:#6b4e3d;
  --band:#eef1f4;
  --row-alt:#e4ebef;
  --line:#dfe3e6;
  --footer:#2f333e;
  --grey-btn:#d6dadd;
}
*{box-sizing:border-box;margin:0;padding:0}
html,body{width:714px;height:1200px;overflow:hidden}
body{font-family:"Lato",sans-serif;color:var(--ink);background:#fff;position:relative}
a{color:inherit;text-decoration:none}

.site-header{height:50px;border-top:2px solid var(--orange);background:#fff;position:relative;box-shadow:0 1px 3px rgba(0,0,0,.08);z-index:2}
.logo{position:absolute;left:50px;top:13px;font-size:17px;font-weight:700;color:var(--teal);letter-spacing:-.2px}
.main-nav{position:absolute;right:70px;top:0;display:flex;height:48px;font-size:8.5px;color:#555}
.main-nav a{padding:0 12px;line-height:44px;position:relative}
.main-nav a.active{color:var(--teal)}
.main-nav a.active::after{content:"";position:absolute;left:6px;right:6px;bottom:0;height:2px;background:var(--teal)}
.nav-search{position:absolute;right:50px;top:13px;width:20px;height:20px;border-left:1px solid var(--line);padding-left:10px}

.hero{height:232px;position:relative;background:linear-gradient(90deg,#eae4dd,#f2eeea 55%,#e0d9cf)}
.hero-photo{position:absolute;left:380px;top:26px;width:334px;height:206px;background:radial-gradient(ellipse at 30% 60%,#d8c9a4 0%,#7f8a5a 30%,rgba(200,190,170,0) 70%)}
.hero h1{position:absolute;left:50px;top:58px;font-family:"Lobster",cursive;font-weight:400;font-size:26px;line-height:33px;color:var(--hero-title)}
.btn{display:inline-block;font-size:7.5px;font-weight:700;border-radius:2px}
.btn-orange{background:var(--orange);color:#fff}
.hero .btn{position:absolute;left:50px;top:136px;width:83px;height:22px;line-height:22px;text-align:center}

.welcome{height:240px;position:relative}
.welcome h2{position:absolute;left:50px;top:22px;font-size:17px;font-weight:400;color:#444;width:455px;padding-bottom:7px;border-bottom:1px solid var(--line)}
.welcome h2 span{color:var(--teal);font-weight:700}
.welcome p{position:absolute;left:50px;width:436px;font-size:7.4px;line-height:14px;color:var(--muted)}
.welcome .p1{top:68px}
.welcome .p2{top:137px}
.welcome .btn{position:absolute;left:50px;top:186px;width:66px;height:19px;line-height:19px;text-align:center;font-weight:400}
.owner-photo{position:absolute;left:505px;top:24px;width:158px;height:193px;border:4px solid #eee;background:linear-gradient(160deg,#c9c9c9,#6b6b6b);box-shadow:0 5px 6px rgba(0,0,0,.12)}

.reviews{height:612px;background:var(--band);position:relative}
.catalog{position:absolute;left:50px;top:20px;width:417px}
.catalog h2{font-size:16px;font-weight:400;color:#333}
.catalog h2 b{font-weight:700}
.catalog .intro{margin-top:10px;font-size:6.9px;line-height:13px;color:var(--muted)}
.review-table{margin-top:11px;width:417px;border-collapse:collapse;font-size:7px;color:#555}
.review-table th{background:var(--teal);color:#fff;height:30px;font-size:7.5px;font-weight:700;border-right:1px solid rgba(255,255,255,.4)}
.review-table td{height:51px;vertical-align:middle;border-right:1px solid #e1e6e9;line-height:11.5px;background:#fff}
.review-table tr:nth-child(odd) td{background:var(--row-alt)}
.review-table td b{font-weight:700}
.col-name{width:98px;padding-left:12px}
.col-photo{width:38px;text-align:center}
.col-origin{width:106px;padding-left:12px}
.col-score{width:106px;padding-left:15px}
.col-score .k{display:inline-block;width:32px;text-align:right;font-weight:700;margin-right:2px}
.col-link{width:69px;text-align:center}
.thumb{display:inline-block;width:28px;height:26px;background:linear-gradient(180deg,#f6ead8,#d99a5f)}
.btn-green{background:var(--green);color:#fff;width:50px;height:19px;line-height:19px;font-weight:400}
.btn-grey{background:var(--grey-btn);color:#555;font-weight:400;height:22px;line-height:22px;display:inline-flex;align-items:center;gap:5px;padding:0 12px}
.catalog .btn-grey{margin-top:21px}

.sidebar{position:absolute;left:490px;top:0;width:174px;height:612px;background:#fff;padding:18px 12px 0}
.sidebar h2{font-size:16px;font-weight:400;color:#333;margin-bottom:10px}
.sidebar h2 b{font-weight:700}
.post{border-bottom:1px solid var(--line);padding-bottom:10px;margin-bottom:12px;position:relative}
.post:last-of-type{border-bottom:0}
.post-img{height:65px}
.post h3{font-size:7.4px;color:var(--teal);line-height:12px;margin-top:6px}
.post .meta{font-size:6.8px;color:#999;margin:3px 0 5px}
.post .meta i{font-style:normal;margin:0 5px}
.post dl{font-size:6.8px;line-height:13px;color:#555}
.post dt{display:inline;font-weight:700;color:#444}
.post dd{display:inline}
.post .more{position:absolute;right:0;bottom:12px;font-size:7px;color:var(--teal)}
.sidebar .btn-grey{margin:2px 0 0 34px}

.site-footer{position:absolute;left:0;top:1134px;width:714px;height:66px;background:var(--footer);color:#eee}
.foot-nav{position:absolute;left:50px;top:21px;font-size:7.2px;display:flex}
.foot-nav span{margin:0 10px}
.copyright{position:absolute;left:50px;top:38px;font-size:7px}
.social{position:absolute;right:50px;top:24px;display:flex;gap:6px}
.social span{width:16px;height:16px;background:#4a4f5c;border-radius:1px}
</style>
</head>
<body>

<header class="site-header">
  <a class="logo" href="#">TopWhiskerTonic.net</a>
  <nav class="main-nav">
    <a class="active" href="#">Home</a>
    <a href="#">About Me</a>
    <a href="#">Our Charter</a>
    <a href="#">Beard Oil Methodology</a>
    <a href="#">BLog</a>
  </nav>
  <svg class="nav-search" viewBox="0 0 20 20" aria-label="Search"><circle cx="14" cy="9" r="3.5" fill="none" stroke="#bbb" stroke-width="1.6"/><line x1="16.5" y1="11.5" x2="19" y2="14" stroke="#bbb" stroke-width="1.8"/></svg>
</header>

<section class="hero">
  <div class="hero-photo" role="img" aria-label="Bottle of beard oil beside a sprig of green cedar on linen"></div>
  <h1>Beard Oil with Argan Kukui<br>Babbasu Citrus Mint Essential Oils</h1>
  <a class="btn btn-orange" href="#">Get Yours Now</a>
</section>

<section class="welcome">
  <h2>Welcome to <span>TopWhiskerTonic</span></h2>
  <p class="p1">Sed ut perspiciatis unde omnis iste natus error sit voluptatem accusantium doloremque laudantium, totam rem aperiam, eaque ipsa quae ab illo inventore veritatis et quasi architecto beatae vitae dicta sunt explicabo. Nemo enim ipsam voluptatem quia voluptas sit aspernatur aut odit aut fugit, sed quia consequuntur magni dolores eos qui ratione voluptatem sequi nesciunt. Neque porro quisquam est, qui dolorem ipsum quia dolor sit amet, consectetur, adipisci velit, sed quia non numquam eius modi tempora incidunt ut labore et dolore magnam aliquam quaerat voluptatem.</p>
  <p class="p2">Sed ut perspiciatis unde omnis iste natus error sit voluptatem accusantium doloremque laudantium, totam rem aperiam, eaque ipsa quae ab illo inventore veritatis et quasi architecto beatae vitae dicta sunt explicabo.</p>
  <a class="btn btn-orange" href="#">Read More »</a>
  <div class="owner-photo" role="img" aria-label="Black and white photo of Delvin Marsk giving a thumbs up"></div>
</section>

<section class="reviews">
  <div class="catalog">
    <h2>The World’s <b>#1</b> Beard Oil Authority</h2>
    <p class="intro">Here is the master list of beard oils reviewed to date. You can link directly to the corresponding review by clicking on the name of the beard oil. In accordance with our charter, we are actively working to locate and review every single beard oil available on the planet Earth.</p>
    <table class="review-table">
      <thead><tr><th>Supplier &amp; Name</th><th>Photo</th><th>Origin,Base Oil,Scent</th><th>Affect,Value,Overall</th><th>Links</th></tr></thead>
      <tbody>
        <tr><td class="col-name">S: Northfield Beard Co.<br>N: Woodsman</td><td class="col-photo"><span class="thumb" role="img" aria-label="Beard oil bottle"></span></td><td class="col-origin">0:&nbsp; Spiciatis<br>B:&nbsp; Modi Tempora<br>S:&nbsp; Quia</td><td class="col-score"><span class="k">Affect:</span> 07<br><span class="k">Value:</span> 05<br><span class="k">Overall:</span> 04</td><td class="col-link"><a class="btn btn-green" href="#">Get Now</a></td></tr>
        <tr><td class="col-name">S: Timberline Soaps<br>N: Lumberjack</td><td class="col-photo"><span class="thumb" role="img" aria-label="Beard oil bottle"></span></td><td class="col-origin">0:&nbsp; Spiciatis<br>B:&nbsp; Modi Tempora<br>S:&nbsp; Quia</td><td class="col-score"><span class="k">Affect:</span> 07<br><span class="k">Value:</span> 05<br><span class="k">Overall:</span> 04</td><td class="col-link"><a class="btn btn-green" href="#">Get Now</a></td></tr>
        <tr><td class="col-name">S: Ironjaw Men's<br>N: Lumberjack</td><td class="col-photo"><span class="thumb" role="img" aria-label="Beard oil bottle"></span></td><td class="col-origin">0:&nbsp; Spiciatis<br>B:&nbsp; Modi Tempora<br>S:&nbsp; Quia</td><td class="col-score"><span class="k">Affect:</span> 07<br><span class="k">Value:</span> 05<br><span class="k">Overall:</span> 04</td><td class="col-link"><a class="btn btn-green" href="#">Get Now</a></td></tr>
        <tr><td class="col-name">S: Bristle Rogue<br>N: Woodsman</td><td class="col-photo"><span class="thumb" role="img" aria-label="Beard oil bottle"></span></td><td class="col-origin">0:&nbsp; Spiciatis<br>B:&nbsp; Modi Tempora<br>S:&nbsp; Quia</td><td class="col-score"><span class="k">Affect:</span> 07<br><span class="k">Value:</span> 05<br><span class="k">Overall:</span> 04</td><td class="col-link"><a class="btn btn-green" href="#">Get Now</a></td></tr>
        <tr><td class="col-name">S: Northfield Beard Co.<br>N: Woodsman</td><td class="col-photo"><span class="thumb" role="img" aria-label="Beard oil bottle"></span></td><td class="col-origin">0:&nbsp; Spiciatis<br>B:&nbsp; Modi Tempora<br>S:&nbsp; Quia</td><td class="col-score"><span class="k">Affect:</span> 07<br><span class="k">Value:</span> 05<br><span class="k">Overall:</span> 04</td><td class="col-link"><a class="btn btn-green" href="#">Get Now</a></td></tr>
        <tr><td class="col-name">S: Timberline Soaps<br>N: Lumberjack</td><td class="col-photo"><span class="thumb" role="img" aria-label="Beard oil bottle"></span></td><td class="col-origin">0:&nbsp; Spiciatis<br>B:&nbsp; Modi Tempora<br>S:&nbsp; Quia</td><td class="col-score"><span class="k">Affect:</span> 07<br><span class="k">Value:</span> 05<br><span class="k">Overall:</span> 04</td><td class="col-link"><a class="btn btn-green" href="#">Get Now</a></td></tr>
        <tr><td class="col-name">S: Ironjaw Men's<br>N: Lumberjack</td><td class="col-photo"><span class="thumb" role="img" aria-label="Beard oil bottle"></span></td><td class="col-origin">0:&nbsp; Spiciatis<br>B:&nbsp; Modi Tempora<br>S:&nbsp; Quia</td><td class="col-score"><span class="k">Affect:</span> 07<br><span class="k">Value:</span> 05<br><span class="k">Overall:</span> 04</td><td class="col-link"><a class="btn btn-green" href="#">Get Now</a></td></tr>
        <tr><td class="col-name">S: Bristle Rogue<br>N: Woodsman</td><td class="col-photo"><span class="thumb" role="img" aria-label="Beard oil bottle"></span></td><td class="col-origin">0:&nbsp; Spiciatis<br>B:&nbsp; Modi Tempora<br>S:&nbsp; Quia</td><td class="col-score"><span class="k">Affect:</span> 07<br><span class="k">Value:</span> 05<br><span class="k">Overall:</span> 04</td><td class="col-link"><a class="btn btn-green" href="#">Get Now</a></td></tr>
      </tbody>
    </table>
    <a class="btn btn-grey" href="#"><svg width="9" height="9" viewBox="0 0 10 10"><path d="M8.5 5A3.5 3.5 0 1 1 7 2.2" fill="none" stroke="#666" stroke-width="1.1"/><path d="M6 0.8 8 2.3 6.2 3.8" fill="none" stroke="#666" stroke-width="1.1"/></svg>View More Beard Oil</a>
  </div>

  <aside class="sidebar">
    <h2>Latest <b>Blog</b></h2>
    <article class="post">
      <div class="post-img" role="img" aria-label="Beard oil bottle on a wooden table" style="background:linear-gradient(135deg,#d9b98f,#8a6a4a)"></div>
      <h3>Hazy Ridge Beard Oil by Old Kettle Grooming</h3>
      <p class="meta">February 12, 2016<i>I</i>Delvin Marsk</p>
      <dl><dt>Oil Name:</dt> <dd>Hazy Ridge Beard</dd><br><dt>Supplier:</dt> <dd>Old Kettle Grooming</dd><br><dt>Sample Size:</dt> <dd>25ml</dd></dl>
      <span class="more">[+]</span>
    </article>
    <article class="post">
      <div class="post-img" role="img" aria-label="Dropper releasing beard oil against green trees" style="background:linear-gradient(135deg,#4d6b3a,#1f2f1c)"></div>
      <h3>Hazy Ridge Beard Oil by Old Kettle Grooming</h3>
      <p class="meta">February 12, 2016<i>I</i>Delvin Marsk</p>
      <dl><dt>Oil Name:</dt> <dd>Hazy Ridge Beard</dd><br><dt>Supplier:</dt> <dd>Old Kettle Grooming</dd><br><dt>Sample Size:</dt> <dd>25ml</dd></dl>
      <span class="more">[+]</span>
    </article>
    <article class="post">
      <div class="post-img" role="img" aria-label="Cloth pouch of beard oil on a wooden table" style="background:linear-gradient(135deg,#e2a868,#b56a2e)"></div>
      <h3>Hazy Ridge Beard Oil by Old Kettle Grooming</h3>
      <p class="meta">February 12, 2016<i>I</i>Delvin Marsk</p>
      <dl><dt>Oil Name:</dt> <dd>Hazy Ridge Beard</dd><br><dt>Supplier:</dt> <dd>Old Kettle Grooming</dd><br><dt>Sample Size:</dt> <dd>25ml</dd></dl>
      <span class="more">[+]</span>
    </article>
    <a class="btn btn-grey" href="#"><svg width="9" height="9" viewBox="0 0 10 10"><path d="M8.5 5A3.5 3.5 0 1 1 7 2.2" fill="none" stroke="#666" stroke-width="1.1"/><path d="M6 0.8 8 2.3 6.2 3.8" fill="none" stroke="#666" stroke-width="1.1"/></svg>View All Blog</a>
  </aside>
</section>

<footer class="site-footer">
  <nav class="foot-nav"><a href="#">Home</a><span>I</span><a href="#">About Me</a><span>I</span><a href="#">Our Charter</a><span>I</span><a href="#">Beard Oil Methodology</a><span>I</span><a href="#">BLog</a></nav>
  <p class="copyright">Copyright © 2016 Top Whisker Tonic. All rights reserved.</p>
  <div class="social" aria-label="Social links"><span></span><span></span><span></span><span></span></div>
</footer>

</body>
</html>
```